Computer consultant business card

Bexil Software is a newly started computer consulting company. It's a small one-man company that provides mostly Vornix applications but also websites in collaboration with designers. I'm running this company on the side of full time university studies.

I want the final design to be clean and memorable. Be creative! :)

Some inspiration:
http://www.pixelmarta.com/design/48317
http://www.pixelmarta.com/design/2739164/business-card-design-by-frostlynk
http://www.pixelmarta.com/design/604281/business-card-design-by-koralind-vestrabanu

See attachment for my company logo.
Updates

I would like to thank everyone for submitting! I'll need a couple of days to review and ultimately select a design.

Target Market(s)

Non-technical entrepreneurs and small companies.

Industry/Entity Type

University

Requirements
Must have
• My company logo.
In any way, both colors from my logo.
First- and last name, e-mail and phone number.
Double-sided design.
Nice to have
• Something creative with the symbol in my logo

```html
<!DOCTYPE html>
<html lang="en">
<head>
<meta charset="utf-8">
<title>Bexil Software – Business Card</title>
<link rel="stylesheet" href="https://fonts.googleapis.com/css2?family=Quicksand:wght@400;500;700&display=swap">
<style>
  :root {
    --page-bg: #2b2b2b;
    --card-dark: #353433;
    --card-dark-edge: #2e2d2c;
    --card-light: #f7f7f9;
    --card-light-edge: #dcdde2;
    --brand-blue: #4a8ad0;
    --text-light: #e8e8e8;
    --text-dark: #2f2f2f;
    --divider: #cfcfcf;
  }
  * { margin: 0; padding: 0; box-sizing: border-box; }
  html, body {
    width: 1200px;
    height: 720px;
    overflow: hidden;
    background: var(--page-bg);
    font-family: "Quicksand", sans-serif;
  }
  .canvas {
    position: relative;
    width: 1200px;
    height: 720px;
    display: flex;
    align-items: center;
    justify-content: center;
    gap: 50px;
  }
  .card {
    width: 520px;
    height: 300px;
    border-radius: 2px;
    position: relative;
    display: flex;
    align-items: center;
    box-shadow: 0 10px 30px rgba(0, 0, 0, 0.45);
  }
  .card--front {
    background: radial-gradient(ellipse at 50% 45%, var(--card-dark) 0%, var(--card-dark-edge) 100%);
    padding-left: 120px;
  }
  .card--back {
    background: radial-gradient(ellipse at 45% 45%, #ffffff 0%, var(--card-light) 45%, var(--card-light-edge) 100%);
    justify-content: center;
  }
  .brand {
    display: flex;
    align-items: center;
  }
  .brand__dot {
    border-radius: 50%;
    background: var(--brand-blue);
    flex-shrink: 0;
  }
  .brand__name {
    font-weight: 700;
    line-height: 1;
  }
  .card--front .brand { gap: 10px; }
  .card--front .brand__dot { width: 22px; height: 22px; }
  .card--front .brand__name { color: var(--text-light); font-size: 26px; }
  .card--back .brand { gap: 18px; }
  .card--back .brand__dot { width: 54px; height: 54px; }
  .card--back .brand__name { color: var(--text-dark); font-size: 72px; }
  .divider {
    width: 1px;
    height: 72px;
    background: var(--divider);
    margin: 0 18px 0 20px;
  }
  .contact {
    color: var(--text-light);
    font-size: 15px;
    line-height: 1.32;
    font-weight: 400;
  }
  .contact__name { font-size: 18px; font-weight: 500; margin-bottom: 2px; }
  .contact__first { color: var(--brand-blue); }
  .contact__phone { color: var(--brand-blue); }
</style>
</head>
<body>
  <main class="canvas">
    <section class="card card--front" aria-label="Card front">
      <div class="brand">
        <span class="brand__dot"></span>
        <span class="brand__name">bexil</span>
      </div>
      <span class="divider"></span>
      <div class="contact">
        <p class="contact__name"><span class="contact__first">Tobias</span> Lundvik</p>
        <p class="contact__email">tobias.lundvik@bexil.se</p>
        <p class="contact__phone">073 - 418 52 07</p>
        <p class="contact__web">www.bexil.se</p>
      </div>
    </section>
    <section class="card card--back" aria-label="Card back">
      <div class="brand">
        <span class="brand__dot"></span>
        <span class="brand__name">bexil</span>
      </div>
    </section>
  </main>
</body>
</html>
```